New Property development signage

large poster for a new development.
3 metres x 2 metres. To include the following.

Tresswick Gardens
TO LET
LUXURY FULLY FURNISHED LARGE
2 AND 3 BED APARTMENTS
Garrold Estates
362 4150
www.garroldestates-example.com

Need this to be large simple writing with Garrold estates logo on the bottom

Target Market(s)

High end rental property market

Industry/Entity Type

Real Estate Development

Colors
000000
cbcbcb
0555a3

Requirements
Must have
• Name of the development must be in a different font, classic style
Nice to have
• Light Grey background, blues for colours
Should not have
• anymore than 3 /4 colours

```html
<!DOCTYPE html>
<html lang="en">
<head>
<meta charset="utf-8">
<title>Tresswick Gardens – To Let</title>
<link rel="stylesheet" href="https://fonts.googleapis.com/css2?family=Playfair+Display:wght@700&family=Jost:wght@600&family=Roboto+Condensed:wght@500;600&display=swap">
<style>
  :root {
    --stage: #f2f2f2;
    --poster-grey: #cbcbcb;
    --ink: #000000;
    --brand-blue: #0555a3;
    --white: #ffffff;
  }
  * { box-sizing: border-box; margin: 0; padding: 0; }
  html, body { width: 960px; height: 1200px; overflow: hidden; }
  body {
    background: var(--stage);
    display: flex;
    align-items: center;
    justify-content: center;
  }
  .poster {
    width: 610px;
    height: 1100px;
    background: var(--poster-grey);
    border: 6px solid var(--ink);
    padding: 52px 46px 44px;
    display: flex;
    flex-direction: column;
    justify-content: space-between;
    color: var(--ink);
  }
  .headline { display: flex; flex-direction: column; }
  .development-name {
    font-family: "Playfair Display", serif;
    font-weight: 700;
    text-align: center;
    text-transform: uppercase;
    color: var(--brand-blue);
    line-height: 1.08;
    white-space: nowrap;
  }
  .development-name span { display: block; }
  .development-name .line-first { font-size: 74px; letter-spacing: 2px; }
  .development-name .line-second { font-size: 90px; letter-spacing: 3px; }
  .to-let-band {
    margin-top: 14px;
    background: var(--brand-blue);
    color: var(--white);
    font-family: "Jost", sans-serif;
    font-weight: 600;
    font-size: 132px;
    line-height: 1;
    text-align: center;
    letter-spacing: -2px;
    padding: 4px 0 12px;
  }
  .details { display: flex; flex-direction: column; }
  .offer {
    font-family: "Roboto Condensed", sans-serif;
    font-weight: 500;
    text-align: center;
    text-transform: uppercase;
  }
  .offer p {
    font-size: 33px;
    line-height: 1.55;
    border-bottom: 2px solid var(--ink);
  }
  .website {
    margin-top: 14px;
    font-family: "Roboto Condensed", sans-serif;
    font-weight: 600;
    font-size: 31px;
    text-align: center;
    color: var(--brand-blue);
    white-space: nowrap;
  }
  .agent-panel {
    border: 12px solid var(--ink);
    background: var(--poster-grey);
  }
  .agent-name {
    background: var(--brand-blue);
    color: var(--white);
    font-family: "Roboto Condensed", sans-serif;
    font-weight: 600;
    font-size: 66px;
    text-align: center;
    padding: 34px 0 36px;
    line-height: 1;
    white-space: nowrap;
  }
  .agent-services {
    font-family: "Roboto Condensed", sans-serif;
    font-weight: 500;
    font-size: 22px;
    text-align: center;
    padding: 12px 0;
  }
  .phone {
    display: flex;
    align-items: center;
    gap: 18px;
    font-family: "Roboto Condensed", sans-serif;
    font-weight: 600;
    font-size: 46px;
    line-height: 1;
  }
  .phone::before, .phone::after {
    content: "";
    flex: 1;
    height: 2px;
    background: var(--ink);
  }
</style>
</head>
<body>
  <main class="poster">
    <div class="headline">
      <h1 class="development-name">
        <span class="line-first">Tresswick</span>
        <span class="line-second">Gardens</span>
      </h1>
      <div class="to-let-band">TO LET</div>
    </div>
    <div class="details">
      <div class="offer">
        <p>Luxury fully furnished large</p>
        <p>2 and 3 bed apartments</p>
      </div>
      <div class="website">www.garroldestates-example.com</div>
    </div>
    <div class="agent-panel">
      <div class="agent-name">Garrold Estates</div>
      <div class="agent-services">Sales • Lettings • Management • B.E.R. Certs</div>
    </div>
    <div class="phone">362 4150</div>
  </main>
</body>
</html>
```